Financial investment calculator report for real estae - layout & design

I am looking to Create a web report utilizing the attached information. It is an investment calculator report that will be customized report based on an online calculator. Therefore the report will need to be designed in a manner that a backend developer will be able to build off of.

The report will need to be web based but also printed in PDF format. The report will need to include the calculation format as well as be templeted to add a report user unique profile information like Headshot, Business Logo, Name, Telephone number, email etc.

The report should be modern and clean and easy to read and use a modern clean template design. It should be able to be easily color customized by the end user to produce templets in Red, Blue, Green, and Greyscale.

The report should be no more than 3 pages total with out breaking up the sections.

Section One - Cover sheet including agent bio info, Report Title and property address (both prominent), 400 Character space for property description, Property Pictures (3), and a google Maps integration image showing property location, It should also have room for about 100 words for a text disclaimer. (I will provide text soon)

Section Two - Inputs from the calculator

Section 3 - The Four Benefits & Rates of Return

Once I have a completed/approved form I will have about a half dozen forms/reports that will need to be laid out with a similar aesthetic.

Feel free to ask me any questions. Thank You
Milo

Target Market(s)

This report will be produced by real estate agents forvtheir investor clients. It should denote professionalism

Font styles to use
Sans Serif

Colors
0054AA
0677BA
7BADD7
CADEEF
E8F1F8
00AB8E
00BBA5
67D7C9
C6EFE9
E9F9F6
EB3D1F
EC4F4E
F09395
F8D3D4
FCEDEE

```html
<!DOCTYPE html>
<html lang="en">
<head>
<meta charset="utf-8">
<title>Investment Analysis – 412 Harlow</title>
<link href="https://fonts.googleapis.com/css2?family=Lato:wght@300;400;700&display=swap" rel="stylesheet">
<style>
:root{
  --bg:#eef3fb;
  --paper:#ffffff;
  --ink:#1b1b1f;
  --muted:#55575d;
  --rule:#e2e3e6;
  --band:#f1f1f2;
  --accent:#2c21e3;
  --negative:#e8474c;
  --photo-a:#3e5a44;
  --photo-b:#9fb3b1;
  --map-land:#eef0ea;
  --map-water:#8fb4f3;
}
*{box-sizing:border-box;margin:0;padding:0}
html,body{width:1200px;height:1012px;overflow:hidden;background:var(--bg)}
body{font-family:'Lato',sans-serif;color:var(--ink)}
.stage{position:absolute;left:0;top:0;width:2091px;height:1764px;transform:scale(0.57389);transform-origin:0 0}
.page{position:absolute;top:241px;width:805px;height:1138px;background:var(--paper);box-shadow:0 4px 18px rgba(40,60,110,.08)}
.page--one{left:257px}
.page--two{left:1113px}

.logo-dot{position:absolute;border-radius:50%;background:#000}
.agency-name{position:absolute;font-size:16px;letter-spacing:.2px}
.agency-name b{font-weight:700}
.agency-name span{font-weight:300}

.agent{position:absolute;right:196px;text-align:right;font-size:10.5px;line-height:19px}
.agent-name{font-size:16px;color:var(--accent);line-height:22px}
.agent-name b{font-weight:700}
.agent-name span{font-weight:300}
.agent-phone svg{width:10px;height:10px;vertical-align:-1px;margin-right:12px}
.headshot{position:absolute;z-index:2;border-radius:6px;background:linear-gradient(160deg,var(--photo-b),var(--photo-a) 70%);box-shadow:0 2px 6px rgba(0,0,0,.18)}

.report-title{position:absolute;left:35px;top:128px;font-size:30px;line-height:38px}
.report-title b{font-weight:700}
.report-title span{font-weight:300}
.rule{position:absolute;height:1px;background:var(--rule)}
.rule-accent{position:absolute;height:3px;background:var(--accent)}

.map{position:absolute;left:36px;top:188px;width:324px;height:178px;border-radius:6px;background:linear-gradient(100deg,var(--map-land) 0%,var(--map-land) 68%,var(--map-water) 80%)}

.property-name{font-size:24px;font-weight:700;line-height:28px}
.property-type{font-size:10px;font-weight:700;line-height:14px}
.property-pin{font-size:10px;font-weight:700;display:flex;align-items:center;gap:8px}
.property-pin svg{width:8px;height:11px}
.property-intro{position:absolute;left:390px;top:182px;width:372px}
.property-intro .property-name{margin-bottom:1px}
.property-desc{font-size:7.6px;line-height:12.8px;color:var(--muted);margin:8px 0 10px}
.price{display:flex;justify-content:space-between;align-items:baseline;width:352px;margin-top:10px;font-size:12px;font-weight:700}
.price strong{color:var(--accent);font-size:16px}

.card{position:absolute;background:var(--paper);border-radius:8px;box-shadow:0 1px 6px rgba(0,0,0,.14);padding:11px 22px 0 14px;overflow:hidden}
.page--two .card{padding-left:9px;padding-top:13px}
.section + .section{margin-top:4px}
.page--one .section--depreciation{margin-top:14px}
.sec-head{position:relative;height:27px;background:var(--band);border-radius:4px;display:grid;grid-template-columns:29px 306px 187px 1fr;align-items:center;font-size:12px;font-weight:400;color:var(--ink)}
.page--two .sec-head{grid-template-columns:23px 306px 187px 1fr}
.sec-head::before{content:"";position:absolute;left:12px;top:12px;width:4px;height:4px;border-radius:50%;background:var(--accent)}
.page--two .sec-head::before{left:7px}
.sec-head .title{grid-column:2/4;white-space:nowrap;color:var(--ink)}
.page--one .sec-head .title{grid-column:2}
.sec-head .col{font-size:8px;color:var(--ink)}
.rows{margin-left:40px;margin-top:2px}
.page--two .rows{margin-left:44px}
.row{display:grid;grid-template-columns:167px 135px 187px 1fr;height:19px;align-items:center;border-bottom:1px solid var(--rule);font-size:8px;color:var(--muted);white-space:nowrap}
.row .num{text-align:right}
.row .neg{color:var(--negative)}
.row .c3{grid-column:3}
.row .c2{grid-column:2}
.total{display:grid;grid-template-columns:167px 135px 187px 1fr;height:22px;padding-top:3px;align-items:center;font-size:12px;font-weight:700;position:relative}
.total::before{content:"";position:absolute;top:0;left:302px;right:0;height:3px;background:var(--accent)}
.total.full::before{left:0}
.total .label{grid-column:3}
.total .num{grid-column:4;text-align:right}
.subhead{height:26px;padding-top:10px;font-size:12px;margin-left:40px;font-weight:400}

.footer{position:absolute;left:35px;right:42px;display:flex;justify-content:space-between;font-size:8px;color:var(--muted)}

.heading{position:absolute;left:38px;font-size:20px;color:var(--accent)}
.heading b{font-weight:700}
.heading span{font-weight:300}
.page-two-id{position:absolute;left:37px;top:109px}
.page-two-id .property-type{margin:2px 0 5px}
</style>
</head>
<body>
<div class="stage">

  <section class="page page--one">
    <div class="logo-dot" style="left:35px;top:39px;width:80px;height:80px"></div>
    <div class="agency-name" style="left:128px;top:70px"><b>AGENCYNAME</b> <span>HERE</span></div>

    <div class="agent" style="top:24px">
      <div class="agent-name"><b>SALEMANS</b> <span>NAME</span></div>
      <div class="agent-phone"><svg viewBox="0 0 24 24" fill="none" stroke="#1b1b1f" stroke-width="2"><path d="M22 16.9v3a2 2 0 0 1-2.2 2 19.8 19.8 0 0 1-8.6-3.1 19.5 19.5 0 0 1-6-6A19.8 19.8 0 0 1 2.1 4.2 2 2 0 0 1 4.1 2h3a2 2 0 0 1 2 1.7c.1 1 .4 1.9.7 2.8a2 2 0 0 1-.5 2.1L8 9.9a16 16 0 0 0 6 6l1.3-1.3a2 2 0 0 1 2.1-.4c.9.3 1.8.6 2.8.7a2 2 0 0 1 1.7 2z"/></svg>(555) 214-0396</div>
      <div>agent@northpointhomes.com</div>
    </div>
    <div class="headshot" role="img" aria-label="Agent headshot photo" style="left:622px;top:24px;width:122px;height:133px"></div>

    <h1 class="report-title"><b>Investment</b> <span>Analysis:</span></h1>
    <div class="rule" style="left:35px;top:168px;width:728px"></div>
    <div class="rule-accent" style="left:35px;top:167px;width:257px"></div>

    <div class="map" role="img" aria-label="Map showing the property location"></div>

    <div class="property-intro">
      <div class="property-name">412 HARLOW</div>
      <div class="property-type">15-Plex of 1bd/1bth Apartments</div>
      <p class="property-desc">Urban bliss in this chic 400 sqft apartment. Step into a bright and open space with stylish décor. Relax on a cozy sofa or entertain in the dining area. The well-equipped kitchen features modern appliances and ample storage. Unwind in the tranquil bedroom with a queen-sized bed. Refresh in the pristine bathroom with a walk-in shower. Enjoy high-speed internet, a smart TV, and laundry facilities. Take in city views from the private balcony. Explore trendy cafes, shops, and restaurants nearby. Embrace the perfect blend of comfort and style in this urban sanctuary.</p>
      <div class="property-pin"><svg viewBox="0 0 16 22"><path d="M8 0a8 8 0 0 0-8 8c0 6 8 14 8 14s8-8 8-14a8 8 0 0 0-8-8zm0 11a3 3 0 1 1 0-6 3 3 0 0 1 0 6z" fill="#1b1b1f"/></svg>15-Plex of 1bd/1bth Apartments</div>
      <div class="price"><span>PURCHASE PRICE:</span><strong>$1.690.000</strong></div>
    </div>

    <div class="card" style="left:36px;top:381px;width:728px;height:710px">
      <div class="section">
        <div class="sec-head"><span></span><span class="title">PROPERTY ADDRESS:</span></div>
        <div class="rows">
          <div class="row"><span>Financing</span><span class="c3">20% Down</span><span class="num">20 Year Conventional</span></div>
          <div class="row"><span>Purchase Price</span><span class="num" style="grid-column:4">$1.690.000</span></div>
          <div class="row"><span>Down Payment (Cash Invested)</span><span class="c3">20% of purchase price</span><span class="num">$338.000</span></div>
          <div class="row"><span>Amount Financed</span><span class="num" style="grid-column:4">$1.352.000</span></div>
          <div class="row"><span>Needed Capital Improvements Est</span><span class="num" style="grid-column:4">$0</span></div>
          <div class="row"><span>Est. Closing Costs</span><span class="num" style="grid-column:4">$3.000</span></div>
          <div class="row" style="border-bottom:none"><span style="grid-column:1/3">CASH Invested (Down Pmt. + Closing Costs)</span><span class="num" style="grid-column:4">$341.000</span></div>
          <div class="total full"><span style="grid-column:1">Rate: 7%</span><span style="grid-column:2">Term: 20 years</span><span class="label">Monthly P&amp;I:</span><span class="num">$10.482</span></div>
        </div>
      </div>

      <div class="section section--depreciation">
        <div class="sec-head"><span></span><span class="title">DEPRICIATION (FIRST YEAR): (ASSUMES 80%/20%)</span><span class="col">Est. Value</span><span class="col">Yearly Rate</span></div>
        <div class="rows">
          <div class="row"><span>Land Cost</span><span>0 Year</span><span>$338.000</span><span style="display:flex;justify-content:space-between"><span>0%</span><span>$0</span></span></div>
          <div class="row"><span>Personal Property Cost</span><span>5 Years</span><span>$45.000</span><span style="display:flex;justify-content:space-between"><span>20%</span><span>$9.000</span></span></div>
          <div class="row"><span>Building Cost</span><span>27.5 Years</span><span>$1.262.000</span><span style="display:flex;justify-content:space-between"><span>3.48%</span><span>$43.918</span></span></div>
          <div class="row" style="border-bottom:none"><span>Land Improvement Cost</span><span>15 Years</span><span>$45.000</span><span style="display:flex;justify-content:space-between"><span>5%</span><span>$2.250</span></span></div>
          <div class="total"><span class="label">Total Depreciation:</span><span class="num">$55.168</span></div>
        </div>
      </div>

      <div class="section">
        <div class="sec-head"><span></span><span class="title">INCOME:</span></div>
        <div class="rows">
          <div class="row"><span>Annual Rent</span><span class="num" style="grid-column:4">$170.000</span></div>
          <div class="row"><span>Other Income</span><span class="num" style="grid-column:4">$0</span></div>
          <div class="row" style="border-bottom:none"><span>Less Vacancy</span><span class="c3">est. 5% of annual rent</span><span class="num neg">-$0</span></div>
          <div class="total"><span class="label">Gross Operating Income:</span><span class="num">$170.000</span></div>
        </div>
      </div>

      <div class="section">
        <div class="sec-head"><span></span><span class="title">EXPENSES:</span></div>
        <div class="rows">
          <div class="row"><span>Real Estate Tax</span><span class="num" style="grid-column:4">$27.439</span></div>
          <div class="row"><span>Insurance</span><span class="c3">est.</span><span class="num">$3.492</span></div>
          <div class="row"><span>Association Dues/HOA's</span><span class="num" style="grid-column:4">$0</span></div>
          <div class="row"><span>Management</span><span class="c3">0%</span><span class="num">$0</span></div>
          <div class="row"><span>Utilities</span><span class="num" style="grid-column:4">$9.192</span></div>
        </div>
        <div class="subhead">PROPERTY ADDRESS</div>
        <div class="rows" style="margin-top:0">
          <div class="row"><span>Advertising</span><span class="num" style="grid-column:4">$170.000</span></div>
          <div class="row"><span>Maintnence</span><span class="c3">est.</span><span class="num">$40.123</span></div>
          <div class="row"><span>Miscellaneous1</span><span class="c3">est.</span><span class="num">$129.877</span></div>
          <div class="row" style="border-bottom:none"><span>Miscellaneous2</span><span class="c3">est.</span><span class="num">$125.784</span></div>
          <div class="total"><span class="label">Total Expenses:</span><span class="num">$4.092</span></div>
        </div>
      </div>
    </div>

    <div class="footer" style="top:1108px"><span>412 Harlow, REF #47v8487 | Investment Analysis Report. June 26th, 2023</span><span>Page 1/2</span></div>
  </section>

  <section class="page page--two">
    <div class="logo-dot" style="left:43px;top:13px;width:66px;height:66px"></div>
    <div class="agency-name" style="left:128px;top:37px"><b>AGENCYNAME</b> <span>HERE</span></div>

    <div class="agent" style="top:24px">
      <div class="agent-name"><b>SALEMANS</b> <span>NAME</span></div>
      <div class="agent-phone"><svg viewBox="0 0 24 24" fill="none" stroke="#1b1b1f" stroke-width="2"><path d="M22 16.9v3a2 2 0 0 1-2.2 2 19.8 19.8 0 0 1-8.6-3.1 19.5 19.5 0 0 1-6-6A19.8 19.8 0 0 1 2.1 4.2 2 2 0 0 1 4.1 2h3a2 2 0 0 1 2 1.7c.1 1 .4 1.9.7 2.8a2 2 0 0 1-.5 2.1L8 9.9a16 16 0 0 0 6 6l1.3-1.3a2 2 0 0 1 2.1-.4c.9.3 1.8.6 2.8.7a2 2 0 0 1 1.7 2z"/></svg>(555) 214-0396</div>
      <div>agent@northpointhomes.com</div>
    </div>
    <div class="headshot" role="img" aria-label="Agent headshot photo" style="left:642px;top:26px;width:107px;height:116px"></div>

    <div class="rule" style="left:36px;top:100px;width:728px"></div>
    <div class="rule-accent" style="left:36px;top:99px;width:257px"></div>

    <div class="page-two-id">
      <div class="property-name">412 HARLOW</div>
      <div class="property-type">15-Plex of 1bd/1bth Apartments</div>
      <div class="property-pin"><svg viewBox="0 0 16 22"><path d="M8 0a8 8 0 0 0-8 8c0 6 8 14 8 14s8-8 8-14a8 8 0 0 0-8-8zm0 11a3 3 0 1 1 0-6 3 3 0 0 1 0 6z" fill="#1b1b1f"/></svg>15-Plex of 1bd/1bth Apartments</div>
    </div>

    <h2 class="heading" style="top:222px"><b>The Four</b> <span>Benefits</span></h2>

    <div class="card" style="left:37px;top:252px;width:728px;height:444px">
      <div class="section">
        <div class="sec-head"><span></span><span class="title">CASH FLOW BEFOR TAX:</span></div>
        <div class="rows">
          <div class="row"><span>Gross Operating Income</span><span class="num" style="grid-column:4">$170.000</span></div>
          <div class="row"><span>Operating Expenses</span><span class="num" style="grid-column:4">$40.123</span></div>
          <div class="row"><span>Net Operating Income</span><span class="num" style="grid-column:4">$129.877</span></div>
          <div class="row" style="border-bottom:none"><span style="grid-column:1/3">Annual Debt Service (Monthly P&amp;I x 12)</span><span class="num" style="grid-column:4">$125.784</span></div>
          <div class="total"><span class="label">Chash flow befor tax:</span><span class="num">$4.092</span></div>
        </div>
      </div>
      <div class="section">
        <div class="sec-head"><span></span><span class="title">PRINCIPAL REDUCTION:</span></div>
        <div class="rows">
          <div class="row"><span>Annual Debt Service</span><span class="num" style="grid-column:4">$125.784</span></div>
          <div class="row" style="border-bottom:none"><span>Interest (first year)</span><span class="num neg" style="grid-column:4">-$93.621</span></div>
          <div class="total"><span class="label">Chash flow befor tax:</span><span class="num">$32.163</span></div>
        </div>
      </div>
      <div class="section">
        <div class="sec-head"><span></span><span class="title">TAXES PAID/SAVED:</span></div>
        <div class="rows">
          <div class="row"><span>Net Operating Income</span><span class="num" style="grid-column:4">$129.877</span></div>
          <div class="row"><span>Interest paid in first year</span><span class="num" style="grid-column:4">$93.621</span></div>
          <div class="row"><span>Total Depreciation</span><span class="num" style="grid-column:4">$55.168</span></div>
          <div class="row"><span>Taxable Income</span><span class="num neg" style="grid-column:4">-$18.912</span></div>
          <div class="row" style="border-bottom:none"><span>Tax Bracket</span><span class="c3">28%</span><span class="num neg">-$5.295</span></div>
          <div class="total"><span class="label">Taxes Saved:</span><span class="num">$5.295</span></div>
        </div>
      </div>
      <div class="section">
        <div class="sec-head"><span></span><span class="title">APPRECIATION:</span></div>
        <div class="rows">
          <div class="total"><span class="label">Estimate of Appriciation:</span><span class="num">0%</span></div>
        </div>
      </div>
    </div>

    <h2 class="heading" style="top:719px"><b>Rates of</b> <span>Returns</span></h2>

    <div class="card" style="left:37px;top:749px;width:728px;height:305px">
      <div class="section">
        <div class="sec-head"><span></span><span class="title">RETURN ON INVESTMENT WITHOUT APPRICIATION:</span></div>
        <div class="rows">
          <div class="row"><span style="grid-column:1/3">Cash Flow before Tax + Principal Reduction + Tax Saved</span><span class="num" style="grid-column:4">$30.961</span></div>
          <div class="row" style="border-bottom:none"><span>Cash Invested</span><span class="num" style="grid-column:4">$341.000</span></div>
          <div class="total"><span class="label">ROI w/o Appriciation</span><span class="num">9.08%</span></div>
        </div>
      </div>
      <div class="section">
        <div class="sec-head"><span></span><span class="title">CAPITALIZATION RATE:</span></div>
        <div class="rows">
          <div class="row"><span>Net Operating Income</span><span class="num" style="grid-column:4">$129.877</span></div>
          <div class="row" style="border-bottom:none"><span>Purchase Cost</span><span class="num" style="grid-column:4">$1.690.000</span></div>
          <div class="total"><span class="label">Capitalization Rate:</span><span class="num">7.69%</span></div>
        </div>
      </div>
      <div class="section">
        <div class="sec-head"><span></span><span class="title">CASH ON CASH:</span></div>
        <div class="rows">
          <div class="row"><span>Cash Flow before Tax</span><span class="num" style="grid-column:4">$4.092</span></div>
          <div class="row" style="border-bottom:none"><span>Cash Invested</span><span class="num" style="grid-column:4">$341.000</span></div>
          <div class="total"><span class="label">Cash On Cash:</span><span class="num">1.2%</span></div>
        </div>
      </div>
    </div>

    <div class="footer" style="top:1114px;left:36px;right:41px"><span>412 Harlow, REF #47v8487 | Investment Analysis Report. June 26th, 2023</span><span>Page 2/2</span></div>
  </section>

</div>
</body>
</html>
```